Business Card Design

We are a commercial real estate brokerage in San Francisco, leasing office buildings downtown.
I would like a clean, elegant look. Simple but powerful .

Industry/Entity Type

Business

Contact Information for Business Card

Derek Holloway
lic# 07258143
415.555.0172
derek@velt-commercial.example
velt-commercial.example

```html
<!DOCTYPE html>
<html lang="en">
<head>
<meta charset="utf-8">
<title>Velt Commercial — Business Card</title>
<link href="https://fonts.googleapis.com/css2?family=Roboto:wght@400;500;700&display=swap" rel="stylesheet">
<style>
  :root {
    --backdrop: #ece9e4;
    --card: #ffffff;
    --skyline: #e6e7e9;
    --brand: #6f7f9c;
    --name: #58595b;
    --muted: #8593ad;
    --icon: #77787b;
  }
  * { margin: 0; padding: 0; box-sizing: border-box; }
  html, body {
    width: 1200px; height: 695px; overflow: hidden;
    background: var(--backdrop);
    font-family: "Roboto", Arial, sans-serif;
  }
  .card {
    position: absolute; left: 447px; top: 87px;
    width: 306px; height: 520px;
    background: var(--card);
    overflow: hidden;
    box-shadow: 0 1px 4px rgba(0,0,0,0.12);
  }
  .brand {
    position: absolute; top: 70px; left: 0; width: 100%;
    text-align: center; color: var(--brand); font-weight: 500;
  }
  .brand-name { display: block; font-size: 36px; line-height: 36px; letter-spacing: 1px; }
  .brand-sub { display: block; font-size: 17px; line-height: 22px; letter-spacing: 0.5px; }
  .skyline {
    position: absolute; left: 0; top: 243px; width: 100%; height: 277px;
    background: linear-gradient(180deg, #e9eaec 0%, var(--skyline) 100%);
  }
  .contact { position: absolute; left: 44px; top: 377px; }
  .person-name { font-size: 15px; font-weight: 700; color: var(--name); margin-left: 12px; line-height: 20px; }
  .license { font-size: 14px; color: var(--muted); margin-left: 12px; line-height: 18px; margin-bottom: 2px; }
  .line {
    display: flex; align-items: center; gap: 4px;
    font-size: 13px; font-weight: 700; color: var(--brand); line-height: 16.5px;
  }
  .line svg { width: 8px; height: 8px; flex: none; }
</style>
</head>
<body>
  <div class="card">
    <div class="brand">
      <span class="brand-name">VELT</span>
      <span class="brand-sub">COMMERCIAL</span>
    </div>

    <div class="skyline" role="img" aria-label="Pale grey silhouette of downtown office towers along the lower card"></div>

    <div class="contact">
      <p class="person-name">Derek Holloway</p>
      <p class="license">lic# 07258143</p>
      <p class="line">
        <svg viewBox="0 0 8 8" aria-hidden="true"><circle cx="4" cy="4" r="3.5" fill="var(--icon)"/><rect x="2.5" y="2" width="3" height="4" rx="0.6" fill="#fff"/></svg>
        415.555.0172
      </p>
      <p class="line">
        <svg viewBox="0 0 8 8" aria-hidden="true"><circle cx="4" cy="4" r="3.5" fill="var(--icon)"/><rect x="2" y="2.7" width="4" height="2.8" fill="#fff"/><path d="M2 2.8 L4 4.3 L6 2.8" stroke="var(--icon)" stroke-width="0.6" fill="none"/></svg>
        derek@velt-commercial.example
      </p>
      <p class="line">
        <svg viewBox="0 0 8 8" aria-hidden="true"><circle cx="4" cy="4" r="3.3" fill="none" stroke="var(--icon)" stroke-width="0.8"/><ellipse cx="4" cy="4" rx="1.4" ry="3.3" fill="none" stroke="var(--icon)" stroke-width="0.6"/><line x1="0.7" y1="4" x2="7.3" y2="4" stroke="var(--icon)" stroke-width="0.6"/></svg>
        velt-commercial.example
      </p>
    </div>
  </div>
</body>
</html>
```